Website Design for a different kind of Business Consulting organisation needed!

We need a website design that reflects who we are, the simplicity of our consulting business and with a focus on our priority - to help our clients deliver, or execute - the "e" in Vantor-i.

Our key high level requirements are:
1) Simple and intuitive look and feel
2) Integration with all key social media platforms, twitter, facebook, linkedin, tumblr.

10 pages, tops.
- Main page - Welcome
- About Us/ Who are Vantor-i?
- 5 services pages - Project Management, Business Process Management, Change Management, Business Analysis and Finance Systems
- Contact Us

Something like:
http://www.lumvexhold.example/

Vantor-i is a registered trademark and all Logos and other branded material are attached for reference.

So, what’s our gig: A few snippets from previous work...

We are a different kind of business consulting group. We partner with our clients to help them deliver change. We don't just provide them with the theory. We also provide them with the leadership and capability to execute the change.

We aren’t a one stop shop, and we don’t offer cookie cutter solutions. We’re a boutique consulting firm covering Project Management, Business Process Management, Change Management and Business Analytics.

Vantor-i is a professional services organisation that partners with their clients to lead the execution of strategic process and system improvement initiatives. Vantor-i combines hands on delivery with coaching in best practice methodologies and approaches to build their clients capabilities to ensure their ongoing success in project implementations.

UPDATES:

Thanks to everyone who has submitted designs so far. The standard of designs coming through is quite high, with lots of professional designs that nail the design brief. Eliminating them is proving to be quite challenging.

A few updates to the job brief:
- Please make sure the design fits on one page. We would like all of our information to be on the first page that people see without them having to scroll down
- Please ensure you include the FIVE services we offer in the design
- Please use corporate images/istock photos in your designs which are relevant to our business
- Please add a section for a live twitter feed from our twitter account and a link to google+
- Please add a section for news/updates

Also, if you are able to build a site once a design is selected, please let us know.

Thanks,

Maribel.

Target Market(s)

Our target customers are large enterprises in Australia that are growing rapidly and have recently (last 24 months) undertaken or are currently undergoing software implementations and business process improvement programs. These businesses have a turnover of $100m or above and are working hard to differentiate themselves from their competitors but are not seeing the return on investment promised by software vendors and process improvement initiatives.

Industry/Entity Type

Leadership

Requirements
Must have
• Collaboration / Training / Workshop / Consulting images all of a professional nature.
Simple, non-cluttered look with plenty of white space.

```html
<!DOCTYPE html>
<html lang="en">
<head>
<meta charset="utf-8">
<title>Vantor-i — Professional Services</title>
<link href="https://fonts.googleapis.com/css2?family=Jura:wght@500;600&family=Arimo:ital,wght@0,400;1,400&family=Roboto+Condensed:ital,wght@1,300&display=swap" rel="stylesheet">
<style>
  :root {
    --brand: #0c5cb3;
    --tab-1: #5aadf0;
    --tab-2: #3d93e3;
    --tab-3: #1a74d0;
    --tab-4: #0d62bf;
    --tab-5: #0a4a94;
    --ink: #333333;
    --muted: #555555;
    --panel: #f4f4f4;
    --rule: #d6d6d6;
    --white: #ffffff;
  }
  * { box-sizing: border-box; margin: 0; padding: 0; }
  html, body { width: 1200px; height: 1161px; overflow: hidden; background: var(--white); }
  body { position: relative; font-family: "Arimo", Arial, sans-serif; color: var(--ink); }

  .brand-box {
    position: absolute; left: 172px; top: 63px; width: 214px; height: 134px;
    background: var(--brand); z-index: 3;
    display: flex; align-items: center; justify-content: center;
  }
  .brand-name { font-family: "Arimo", Arial, sans-serif; font-weight: 400; font-size: 32px; color: var(--white); }

  .main-nav { position: absolute; left: 386px; top: 90px; width: 644px; height: 48px; display: flex; }
  .main-nav a {
    flex: 1; display: flex; align-items: center; justify-content: center;
    font-family: "Jura", sans-serif; font-weight: 500; font-size: 17px; color: var(--white); text-decoration: none;
  }
  .main-nav a:nth-child(1) { background: var(--tab-1); }
  .main-nav a:nth-child(2) { background: var(--tab-2); }
  .main-nav a:nth-child(3) { background: var(--tab-3); }
  .main-nav a:nth-child(4) { background: var(--tab-4); }
  .main-nav a:nth-child(5) { background: var(--tab-5); }

  .hero {
    position: absolute; left: 172px; top: 138px; width: 858px; height: 351px;
    background: linear-gradient(100deg, #6f6a66 0%, #c9c4c0 30%, #3a3635 55%, #a9a8a6 80%, #d8d8d6 100%);
  }
  .hero-caption {
    position: absolute; left: 525px; top: 232px; width: 320px;
    font-family: "Roboto Condensed", sans-serif; font-style: italic; font-weight: 300;
    font-size: 23px; line-height: 34px; color: var(--white);
  }
  .hero-arrows { position: absolute; right: 11px; bottom: 13px; display: flex; gap: 2px; }
  .hero-arrows span { width: 18px; height: 17px; background: rgba(255,255,255,0.15); }

  .news {
    position: absolute; left: 172px; top: 511px; width: 858px; height: 86px;
    background: var(--panel); border: 1px solid var(--rule); border-left: 5px solid var(--brand);
    padding: 13px 24px 0 21px;
  }
  .news h2 { font-family: "Jura", sans-serif; font-weight: 600; font-size: 15px; color: var(--brand); margin-bottom: 8px; }
  .news p { font-style: italic; font-size: 9px; line-height: 17.5px; color: var(--ink); }
  .news-arrows { position: absolute; right: 20px; top: 15px; display: flex; gap: 6px; }

  .services { position: absolute; left: 172px; top: 621px; width: 858px; height: 127px; }
  .service-tile { position: absolute; top: 0; width: 200px; height: 127px; }
  .service-tile .photo { position: absolute; inset: 0; }
  .service-tile .label {
    position: absolute; left: 0; right: 0; bottom: 0; height: 26px;
    background: rgba(20,20,20,0.82); color: var(--white);
    font-family: "Jura", sans-serif; font-weight: 500; font-size: 13px;
    padding-left: 11px; line-height: 26px;
  }

  .about { position: absolute; left: 172px; top: 783px; width: 858px; text-align: center; }
  .about h2 { font-family: "Jura", sans-serif; font-weight: 600; font-size: 15px; color: var(--brand); margin-bottom: 10px; }
  .about p { font-size: 9px; line-height: 19px; color: var(--ink); }

  .site-footer {
    position: absolute; left: 172px; top: 905px; width: 858px; height: 210px;
    border-top: 1px solid #e2e2e2;
    background: linear-gradient(#f4f4f4 0%, #ffffff 60px);
  }
  .footer-brand { position: absolute; left: 45px; top: 66px; font-family: "Arimo", Arial, sans-serif; font-weight: 400; font-size: 30px; color: var(--brand); }
  .social { position: absolute; left: 48px; top: 121px; display: flex; gap: 4.6px; }
  .social span { width: 20px; height: 20px; border-radius: 50%; background: #d4d4d4; }
  .copyright { position: absolute; left: 48px; top: 163px; font-size: 9px; line-height: 20px; color: var(--ink); }
  .link-col { position: absolute; top: 35px; list-style: none; }
  .link-col li { font-size: 9px; line-height: 19.7px; color: var(--muted); }
  .link-col li::before { content: "›"; margin-right: 6px; color: #888; }
</style>
</head>
<body>
  <div class="brand-box"><span class="brand-name">Vantor-i</span></div>

  <nav class="main-nav">
    <a href="#">Services</a><a href="#">Careers</a><a href="#">FAQ's</a><a href="#">Clients</a><a href="#">Testimonials</a>
  </nav>

  <section class="hero" role="img" aria-label="Photo of two consultants reviewing documents at a boardroom table">
    <p class="hero-caption">Vantor-i is a professional services organisation</p>
    <div class="hero-arrows"><span></span><span></span></div>
  </section>

  <section class="news">
    <h2>Recent news</h2>
    <p>Many desktop publishing packages and web page editors now use Lorem Ipsum as their default model text, and a search for 'lorem ipsum' will uncover many web sites still in their infancy.<br>Various versions have evolved over the years, sometimes by accident, sometimes on purpose</p>
    <div class="news-arrows">
      <svg width="6" height="9" viewBox="0 0 6 9"><path d="M5 1 1 4.5 5 8" fill="none" stroke="#999" stroke-width="1.3"/></svg>
      <svg width="6" height="9" viewBox="0 0 6 9"><path d="M1 1 5 4.5 1 8" fill="none" stroke="#999" stroke-width="1.3"/></svg>
    </div>
  </section>

  <section class="services">
    <div class="service-tile" style="left:0">
      <div class="photo" role="img" aria-label="Photo of a businessman beside a chalk growth chart" style="background:linear-gradient(135deg,#8a8a8a,#4e4e4e)"></div>
      <div class="label">Strategic process »</div>
    </div>
    <div class="service-tile" style="left:219px">
      <div class="photo" role="img" aria-label="Photo of a man framing a view with his hands" style="background:linear-gradient(135deg,#e6e2de,#a89b92)"></div>
      <div class="label">System improvement »</div>
    </div>
    <div class="service-tile" style="left:439px">
      <div class="photo" role="img" aria-label="Photo of a man working at a desk under open sky" style="background:linear-gradient(180deg,#2f6fc0,#b8c7d6)"></div>
      <div class="label">Practice methodologies »</div>
    </div>
    <div class="service-tile" style="left:658px">
      <div class="photo" role="img" aria-label="Photo of a team meeting around a laptop" style="background:linear-gradient(135deg,#6b5a4c,#c8c4c0)"></div>
      <div class="label">Project implementations »</div>
    </div>
  </section>

  <section class="about">
    <h2>About Vantor-i</h2>
    <p>It is a long established fact that a reader will be distracted by the readable content of a page when looking at its layout. The point of using Lorem Ipsum is that it has a more-or-less normal distribution of<br>letters, as opposed to using 'Content here, content here', making it look like readable English. Many desktop publishing packages and web page editors now use Lorem Ipsum as their default model text,<br>and a search for 'lorem ipsum' will uncover many web sites still in their infancy. Various versions have evolved over the years, sometimes by accident, sometimes on purpose</p>
  </section>

  <footer class="site-footer">
    <div class="footer-brand">Vantor-i</div>
    <div class="social"><span></span><span></span><span></span><span></span><span></span><span></span></div>
    <p class="copyright">Copyright © 2014. Vantor-i.<br>All rights reserved</p>
    <ul class="link-col" style="left:256px">
      <li>Home</li><li>About</li><li>News</li><li>Services</li><li>Careers</li><li>FAQ's</li><li>Clients</li><li>Testimonials</li><li>Contact</li>
    </ul>
    <ul class="link-col" style="left:358px">
      <li>Taxation</li><li>International</li><li>Corporate</li><li>Individual</li>
    </ul>
    <ul class="link-col" style="left:486px">
      <li>Accounting &amp; Advisory</li><li>Compliance &amp; Reporting</li><li>Audit</li><li>Valuations &amp; Corporate Review</li><li>Cashflow Management</li><li>Succession Planning</li><li>Forensic Accounting</li><li>Virtual CFO</li>
    </ul>
    <ul class="link-col" style="left:693px">
      <li>Pensions</li><li>International Pension Funds</li><li>Pension Transfers</li><li>QROPS</li><li>Australian SMSF</li>
    </ul>
  </footer>
</body>
</html>
```